Velk Partners Building Business Cards

We need a business card that reflects our business as "Solar Experts" in San Diego. Browse our website www.velkpartners.example our License needs to be displayed as "CSLB# 3867140" our phone number is (619) 555-0187

Save thousands on your electric bills and increase the value of your home while helping to protect the environment. Our solar installation experts will help you design the system that's right for you, using only the highest quality equipment that will look great and give you ideal performance. Our goal is to make you energy independent, and get your electric bill to 0.

Paul Osterby
(619) 555-0187
paul@velkpartners.example

Target Market(s)

Home owners in san diego looking for solar

Industry/Entity Type

Solar Energy

Contact Information for Business Card

Paul Osterby
(619) 555-0187
paul@velkpartners.example

Font styles to use
Other font styles liked:
• Use our logo font

Requirements
Must have
• License needs to be displayed as "CSLB# 3867140" our phone number is (619) 555-0187
Nice to have
• Real images of rooftop home solar in san diego
Should not have
• our business address

```html
<!DOCTYPE html>
<html lang="en">
<head>
<meta charset="utf-8">
<title>Velk Partners Building – Business Card</title>
<link rel="stylesheet" href="https://fonts.googleapis.com/css2?family=PT+Sans:wght@400;700&display=swap">
<style>
  :root {
    --backdrop: #000000;
    --card: #323335;
    --brand-blue: #23448f;
    --gold: #f2b217;
    --rule: #9a7a22;
    --text: #f1f1f1;
  }
  * { margin: 0; padding: 0; box-sizing: border-box; }
  html, body {
    width: 1200px; height: 900px; overflow: hidden;
    background: var(--backdrop);
    font-family: "PT Sans", "Myriad Pro", Arial, sans-serif;
  }
  .canvas { position: relative; width: 1200px; height: 900px; }
  .card {
    position: absolute; top: 271px;
    width: 457px; height: 281px;
    background: var(--card);
    border-radius: 14px;
  }
  .card--front { left: 137px; }
  .card--back { left: 626px; }

  .wordmark {
    position: absolute;
    display: flex; align-items: center; gap: 10px;
    color: var(--brand-blue);
    font-weight: 700;
    white-space: nowrap;
  }
  .wordmark__dot {
    flex: none; border-radius: 50%; background: var(--gold);
  }
  .card--front .wordmark { right: 28px; top: 66px; font-size: 27px; }
  .card--front .wordmark__dot { width: 24px; height: 24px; }
  .card--back .wordmark { left: 0; right: 0; justify-content: center; top: 113px; font-size: 30px; }
  .card--back .wordmark__dot { width: 27px; height: 27px; }

  .holder {
    position: absolute; left: 27px; right: 28px; top: 175px;
    display: flex; align-items: center; gap: 14px;
  }
  .holder__name {
    color: var(--gold); font-weight: 700; font-size: 15px;
    text-transform: uppercase; letter-spacing: 0.2px; white-space: nowrap;
  }
  .holder__rule { flex: 1; height: 1px; background: var(--rule); }

  .license {
    position: absolute; left: 28px; top: 234px;
    font-size: 12.5px; color: var(--text);
  }
  .license__label { color: var(--gold); font-weight: 700; }

  .contact {
    position: absolute; right: 25px; top: 218px;
    list-style: none; text-align: right;
    font-size: 12.5px; color: var(--text); line-height: 17px;
  }
  .contact__item { display: flex; justify-content: flex-end; align-items: center; gap: 6px; }
  .contact__icon { width: 9px; height: 9px; fill: var(--gold); }
</style>
</head>
<body>
<main class="canvas">
  <section class="card card--front" aria-label="Business card front">
    <div class="wordmark"><span class="wordmark__dot"></span>Velk Partners Building Inc</div>

    <div class="holder">
      <span class="holder__name">Paul Osterby</span>
      <span class="holder__rule"></span>
    </div>

    <p class="license"><span class="license__label">LICENSE:</span> CSLB# 3867140</p>

    <ul class="contact">
      <li class="contact__item">(619) 555-0187
        <svg class="contact__icon" viewBox="0 0 24 24" aria-hidden="true"><path d="M6.6 10.8a15.1 15.1 0 0 0 6.6 6.6l2.2-2.2c.3-.3.7-.4 1-.2 1.1.4 2.3.6 3.6.6.6 0 1 .4 1 1V20c0 .6-.4 1-1 1A17 17 0 0 1 3 4c0-.6.4-1 1-1h3.5c.6 0 1 .4 1 1 0 1.3.2 2.5.6 3.6.1.3 0 .7-.2 1z"/></svg>
      </li>
      <li class="contact__item">paul@velkpartners.example
        <svg class="contact__icon" viewBox="0 0 24 24" aria-hidden="true"><path d="M2 5h20v14H2z M2 5l10 8 10-8" fill="var(--gold)"/><path d="M2 6l10 7 10-7" fill="none" stroke="var(--card)" stroke-width="2"/></svg>
      </li>
    </ul>
  </section>

  <section class="card card--back" aria-label="Business card back">
    <div class="wordmark"><span class="wordmark__dot"></span>Velk Partners Building Inc</div>
  </section>
</main>
</body>
</html>
```